Business Card Design - Photographer

I am a landscape photographer and I require a business card design. 

I require two designs:
1)  a double sided business card
 and
b)  a single sided business card 

The single sided design can either be the same as the double sided (with just one side having all the information)....or it can be an entire new design. Its up to you.

My corporate colours are (CMYK):

Blue   69, 32, 0, 0
Grey  72,  64,  47,  31
Green  32,  2,  91,  0
Yellow   0, 19, 92, 0
Orange  0, 39, 75, 0

Colour space in final file should be in CMYK.

The details that need to be included on the card:

- Use the provided Logo
- Name: Wiktor Baranowski
- Email:   sales@vistalumeworks.com.au
- Website:    vistalumeworks.com.au
- Twitter:    twitter.com/vistalumeworks
- Facebook:   facebook.com/vistalumeworks
- Mobile  0417 539 662

Please use the attached template to design the logo to the specified size, including the marked bleed lines. I have also attached my logo in PNG (transparent background) and ai format for you to use.

The final file should be:
- Photoshop version with layers so I can edit the name/text etc. All non vector files should be high resolution at 1039 x 697 pixels at 300 dpi.

I also require a file as:
- Vector based PDF

Anyway questions please contact me.

Thank you

Industry/Entity Type

Landscape

Logo styles of interest
Pictorial/Combination Logo
Abstract Logo
Wordmark Logo
Lettermark Logo
Requirements
Must have
• The details that need to be included on the card:

- Use the provided Logo
- Name: Wiktor Baranowski
- Email: sales@vistalumeworks.com.au
- Website: vistalumeworks.com.au
- Twitter: twitter.com/vistalumeworks
- Facebook: facebook.com/vistalumeworks
- Mobile 0417 539 662

```html
<!DOCTYPE html>
<html lang="en">
<head>
<meta charset="utf-8">
<title>Vistalume Works – Business Card</title>
<link rel="stylesheet" href="https://fonts.googleapis.com/css2?family=Cinzel:wght@400;600&family=PT+Sans:wght@400;700&display=swap">
<style>
  :root {
    --slate: #3d4254;
    --paper: #ffffff;
    --ink: #4a4d58;
    --backdrop: #e9e6e2;
    --shadow: rgba(0, 0, 0, 0.18);
  }
  * { margin: 0; padding: 0; box-sizing: border-box; }
  html, body { width: 1200px; height: 758px; overflow: hidden; }
  body {
    background: var(--backdrop);
    position: relative;
    font-family: "PT Sans", Arial, sans-serif;
  }
  .card {
    position: absolute;
    top: 229px;
    width: 520px;
    height: 300px;
    border-radius: 22px;
    overflow: hidden;
    box-shadow: 0 6px 18px var(--shadow);
  }
  .card--front { left: 60px; background: var(--paper); }
  .card--back { left: 620px; background: var(--slate); }

  .front-band { position: absolute; inset: 0; width: 100%; height: 100%; }

  .brand {
    position: absolute;
    left: 36px;
    top: 50px;
    width: 230px;
    text-align: center;
  }
  .brand-disc {
    width: 96px;
    height: 96px;
    margin: 0 auto;
    border-radius: 50%;
    background: var(--paper);
  }
  .brand-name {
    margin-top: 12px;
    font-family: "Cinzel", Georgia, serif;
    font-weight: 600;
    font-size: 22px;
    letter-spacing: 0.5px;
    color: var(--slate);
    white-space: nowrap;
  }
  .brand-rule {
    height: 1px;
    background: var(--slate);
    margin: 3px 8px 0;
  }
  .brand-tagline {
    margin-top: 4px;
    font-family: "Cinzel", Georgia, serif;
    font-size: 9px;
    letter-spacing: 1.5px;
    color: var(--slate);
  }

  .contact {
    position: absolute;
    left: 300px;
    top: 92px;
    list-style: none;
    font-size: 13.5px;
    color: var(--ink);
    line-height: 20px;
  }
  .contact li { display: flex; align-items: center; gap: 6px; white-space: nowrap; }
  .contact svg { width: 10px; height: 10px; flex: none; fill: var(--ink); }
  .contact .person {
    font-weight: 700;
    color: var(--slate);
    margin-bottom: 2px;
  }
  .address {
    position: absolute;
    left: 316px;
    top: 228px;
    font-size: 13.5px;
    line-height: 19px;
    color: var(--ink);
  }

  .back-mark {
    position: absolute;
    left: 50%;
    top: 50px;
    transform: translateX(-50%);
    text-align: center;
  }
  .back-disc {
    width: 130px;
    height: 130px;
    margin: 0 auto;
    border-radius: 50%;
    background: var(--paper);
  }
  .back-name {
    margin-top: 14px;
    font-family: "Cinzel", Georgia, serif;
    font-weight: 600;
    font-size: 18px;
    color: var(--paper);
    white-space: nowrap;
  }
  .back-url {
    position: absolute;
    left: 0;
    right: 0;
    bottom: 36px;
    text-align: center;
    font-family: "Cinzel", Georgia, serif;
    font-size: 17px;
    letter-spacing: 0.5px;
    color: var(--paper);
  }
</style>
</head>
<body>

<section class="card card--front">
  <svg class="front-band" viewBox="0 0 520 300" preserveAspectRatio="none" aria-hidden="true">
    <polygon points="0,0 520,0 520,58 0,112" fill="var(--slate)"/>
  </svg>

  <div class="brand">
    <div class="brand-disc"></div>
    <div class="brand-name">VISTALUME WORKS</div>
    <div class="brand-rule"></div>
    <div class="brand-tagline">FINE ART PHOTOGRAPHY</div>
  </div>

  <ul class="contact">
    <li class="person">Wiktor Baranowski</li>
    <li>
      <svg viewBox="0 0 10 10"><rect x="2.5" y="0.5" width="5" height="9" rx="1"/></svg>
      0417 539 662
    </li>
    <li>
      <svg viewBox="0 0 10 10"><rect x="0.5" y="2" width="9" height="6.5"/></svg>
      sales@vistalumeworks.com.au
    </li>
    <li>
      <svg viewBox="0 0 10 10"><circle cx="5" cy="5" r="4.3"/></svg>
      www.vistalumeworks.com.au
    </li>
    <li>
      <svg viewBox="0 0 10 10"><rect x="0.5" y="0.5" width="9" height="9" rx="1.5"/></svg>
      vistalumeworks
    </li>
    <li>
      <svg viewBox="0 0 10 10"><rect x="0.5" y="0.5" width="9" height="9" rx="1.5"/></svg>
      vistalumeworks
    </li>
  </ul>

  <p class="address">00, Complex name<br>state, city 0020</p>
</section>

<section class="card card--back">
  <div class="back-mark">
    <div class="back-disc"></div>
    <div class="back-name">VISTALUME WORKS</div>
  </div>
  <p class="back-url">WWW.VISTALUMEWORKS.COM.AU</p>
</section>

</body>
</html>
```